Upmarket Dessert Lounge needs a Business Card Design

We are an upmarket dessert lounge needing a business card to match our image.

We want something that is simple yet beautiful, feminine, classy, sophisticated and elegant. We want it to stand out and don't mind if it is bold.

The design should include our logo and colours of red or maroon with gold highlights. We don't mind if black is used.

Marlow & Quince

Target Market(s)

For those who like to indulge or treat themselves and give in to their temptations on good quality desserts.

Industry/Entity Type

Business

Requirements
Must have
• Must include our logo and our name

Marlow & Quince

M & Q

```html
<!DOCTYPE html>
<html lang="en">
<head>
<meta charset="utf-8">
<title>Marlow &amp; Quince — Business Cards</title>
<link rel="stylesheet" href="https://fonts.googleapis.com/css2?family=Source+Sans+3:wght@300;400;600&display=swap">
<style>
  :root {
    --maroon: #7a1216;
    --cream: #f6d9a0;
    --swirl-on-maroon: rgba(196, 108, 78, 0.30);
    --swirl-on-white: rgba(175, 110, 95, 0.13);
    --paper: #ffffff;
    --backdrop: #ece6df;
  }
  * { margin: 0; padding: 0; box-sizing: border-box; }
  html, body { width: 1200px; height: 759px; overflow: hidden; }
  body {
    background: var(--backdrop);
    font-family: "Source Sans 3", "Helvetica Neue", Arial, sans-serif;
    position: relative;
  }
  .card {
    position: absolute;
    width: 524px;
    height: 300px;
    overflow: hidden;
  }
  .card--maroon { background: var(--maroon); color: var(--cream); }
  .card--white { background: var(--paper); }
  .card--front-plain { left: 53px; top: 54px; }
  .card--back-maroon { left: 623px; top: 52px; }
  .card--front-ornate { left: 53px; top: 390px; }
  .card--back-white { left: 623px; top: 390px; }

  /* scrollwork zones: flourishes sit along the left and right edges */
  .ornament-field { position: absolute; inset: 0; }
  .card--maroon .ornament-field {
    background:
      linear-gradient(to right, var(--swirl-on-maroon) 0%, transparent 24%, transparent 76%, var(--swirl-on-maroon) 100%);
  }
  .card--white .ornament-field {
    background:
      linear-gradient(to right, var(--swirl-on-white) 0%, transparent 26%, transparent 74%, var(--swirl-on-white) 100%);
  }

  .wordmark {
    position: absolute;
    font-weight: 300;
    color: var(--cream);
    text-align: center;
    white-space: nowrap;
    line-height: 1;
    transform: translate(-50%, -50%);
  }
  .wordmark--monogram { font-size: 62px; letter-spacing: 2px; }
  .wordmark--full { font-size: 34px; letter-spacing: 3px; }
  .card--white .wordmark { color: var(--maroon); }
  .card--front-plain .wordmark { left: 157px; top: 150px; }
  .card--front-ornate .wordmark { left: 165px; top: 152px; }
  .card--back-maroon .wordmark,
  .card--back-white .wordmark { left: 262px; top: 150px; }

  .divider {
    position: absolute;
    width: 2px;
    background: linear-gradient(to bottom, transparent, var(--cream) 15%, var(--cream) 85%, transparent);
  }
  .card--front-plain .divider { left: 291px; top: 56px; height: 196px; }
  .card--front-ornate .divider { left: 262px; top: 76px; height: 150px; }

  .contact {
    position: absolute;
    font-size: 13px;
    line-height: 15px;
  }
  .card--front-plain .contact { left: 322px; top: 62px; }
  .card--front-ornate .contact { left: 280px; top: 62px; }
  .contact__name { font-size: 16px; font-weight: 600; margin-bottom: 22px; }
  .contact__name span { font-size: 13px; font-weight: 400; }
  .contact__address { margin-bottom: 40px; }
  .contact__list { list-style: none; }
  .contact__list li { display: flex; align-items: center; gap: 4px; height: 18px; }
  .contact__list svg { width: 10px; height: 10px; flex: none; }
</style>
</head>
<body>

<section class="card card--maroon card--front-plain" aria-label="Card front">
  <div class="wordmark wordmark--monogram">M&amp;Q</div>
  <div class="divider"></div>
  <div class="contact">
    <p class="contact__name">Your name, <span>Title</span></p>
    <p class="contact__address">Street Name, City Name<br>State Zip Code</p>
    <ul class="contact__list">
      <li><svg viewBox="0 0 10 10"><path d="M2 1l2 2-1 1.2c.6 1.2 1.6 2.2 2.8 2.8L7 6l2 2-1.4 1.4C4.5 9.2.8 5.5.6 2.4z" fill="var(--cream)"/></svg>555-014-2368</li>
      <li><svg viewBox="0 0 10 10"><rect x="2.5" y="0.5" width="5" height="9" rx="1" fill="none" stroke="var(--cream)"/><rect x="3.5" y="2" width="3" height="4" fill="var(--cream)"/></svg>555-014-2368</li>
      <li><svg viewBox="0 0 10 10"><rect x="0.5" y="2" width="9" height="6" fill="var(--cream)"/><path d="M0.5 2l4.5 3.5L9.5 2" fill="none" stroke="var(--maroon)"/></svg>info@marlow&amp;quince.com</li>
      <li><svg viewBox="0 0 10 10"><circle cx="5" cy="5" r="4.3" fill="none" stroke="var(--cream)"/><ellipse cx="5" cy="5" rx="2" ry="4.3" fill="none" stroke="var(--cream)"/><path d="M0.7 5h8.6" stroke="var(--cream)"/></svg>www.marlow&amp;quince.com</li>
    </ul>
  </div>
</section>

<section class="card card--maroon card--back-maroon" aria-label="Card back">
  <div class="ornament-field" role="img" aria-label="Faint flourished scrollwork along the card edges"></div>
  <div class="wordmark wordmark--full">MARLOW &amp; QUINCE</div>
</section>

<section class="card card--maroon card--front-ornate" aria-label="Card front with scrollwork">
  <div class="ornament-field" role="img" aria-label="Faint flourished scrollwork along the card edges"></div>
  <div class="wordmark wordmark--monogram">M&amp;Q</div>
  <div class="divider"></div>
  <div class="contact">
    <p class="contact__name">Your name, <span>Title</span></p>
    <p class="contact__address">Street Name, City Name<br>State Zip Code</p>
    <ul class="contact__list">
      <li><svg viewBox="0 0 10 10"><path d="M2 1l2 2-1 1.2c.6 1.2 1.6 2.2 2.8 2.8L7 6l2 2-1.4 1.4C4.5 9.2.8 5.5.6 2.4z" fill="var(--cream)"/></svg>555-014-2368</li>
      <li><svg viewBox="0 0 10 10"><rect x="2.5" y="0.5" width="5" height="9" rx="1" fill="none" stroke="var(--cream)"/><rect x="3.5" y="2" width="3" height="4" fill="var(--cream)"/></svg>555-014-2368</li>
      <li><svg viewBox="0 0 10 10"><rect x="0.5" y="2" width="9" height="6" fill="var(--cream)"/><path d="M0.5 2l4.5 3.5L9.5 2" fill="none" stroke="var(--maroon)"/></svg>info@marlow&amp;quince.com</li>
      <li><svg viewBox="0 0 10 10"><circle cx="5" cy="5" r="4.3" fill="none" stroke="var(--cream)"/><ellipse cx="5" cy="5" rx="2" ry="4.3" fill="none" stroke="var(--cream)"/><path d="M0.7 5h8.6" stroke="var(--cream)"/></svg>www.marlow&amp;quince.com</li>
    </ul>
  </div>
</section>

<section class="card card--white card--back-white" aria-label="Card back, light version">
  <div class="ornament-field" role="img" aria-label="Pale flourished scrollwork along the card edges"></div>
  <div class="wordmark wordmark--full">MARLOW &amp; QUINCE</div>
</section>

</body>
</html>
```